Building technology company seek stationery design and folder design

Letterhead, and a folder design
ideally, I would have two letter head design, one is for one-page bussiness letter. the other one I can use for longer document such report, or analysis regular report page
you can find company logo and overall style at our website:
www.structavolt.example

we are in building technology business, using internet of things technology to improve building energy efficiency to make building greener.

Industry/Entity Type

It Company

Requirements
Must have
• company logo
Nice to have
• techy look abstract graphics, etc.
Should not have
• no comment

```html
<!DOCTYPE html>
<html lang="en">
<head>
<meta charset="utf-8">
<title>StructaVolt Stationery</title>
<link href="https://fonts.googleapis.com/css2?family=Questrial&family=Roboto:wght@400;700&display=swap" rel="stylesheet">
<style>
  :root {
    --backdrop: #dcdcdc;
    --paper: #ffffff;
    --paper-shade: #ececec;
    --brand-green: #9cc63b;
    --folder-green: #b2d64f;
    --folder-green-deep: #a9cf45;
    --ink: #4a4a4a;
    --ink-soft: #6a6a6a;
    --top-rule: #77776a;
    --white: #ffffff;
  }
  html, body {
    margin: 0;
    padding: 0;
    width: 1200px;
    height: 821px;
    overflow: hidden;
    background: var(--backdrop);
  }
  .canvas {
    position: relative;
    width: 1200px;
    height: 821px;
  }
  /* Letterhead */
  .letterhead {
    position: absolute;
    left: 75px;
    top: 114px;
    width: 439px;
    height: 620px;
    background: linear-gradient(90deg, var(--paper) 0%, var(--paper) 30%, var(--paper-shade) 100%);
    border-top: 4px solid var(--top-rule);
    border-bottom: 4px solid var(--brand-green);
    box-sizing: border-box;
    font-family: "Questrial", sans-serif;
    color: var(--ink);
  }
  .letterhead__pattern {
    position: absolute;
    inset: 0;
    background: radial-gradient(ellipse at 70% 40%, rgba(210,210,210,0.35), rgba(255,255,255,0) 70%);
  }
  .brand-lockup {
    position: absolute;
    left: 0;
    right: 0;
    top: 66px;
    display: flex;
    align-items: center;
    justify-content: center;
    gap: 8px;
  }
  .brand-lockup__square {
    width: 14px;
    height: 14px;
    background: var(--brand-green);
  }
  .brand-lockup__name {
    font-family: "Questrial", sans-serif;
    font-size: 17px;
    letter-spacing: 1.5px;
    color: var(--brand-green);
  }
  .letter {
    position: absolute;
    left: 39px;
    top: 176px;
    width: 365px;
  }
  .letter__greeting {
    font-size: 11.5px;
    margin: 0 0 16px;
    color: var(--ink);
  }
  .letter__body p {
    font-size: 6.3px;
    line-height: 9.5px;
    margin: 0 0 9px;
    color: var(--ink-soft);
    text-align: justify;
  }
  .letter__closing {
    font-size: 6.5px;
    margin: 18px 0 10px;
    color: var(--ink-soft);
  }
  .letter__signature {
    width: 80px;
    height: 30px;
    background: linear-gradient(90deg, rgba(156,198,59,0.35), rgba(156,198,59,0.1));
    border-radius: 3px;
  }
  .letterhead__footer {
    position: absolute;
    left: 0;
    right: 0;
    top: 570px;
    text-align: center;
    font-family: "Roboto", sans-serif;
    font-size: 6.4px;
    line-height: 9px;
    color: var(--ink);
  }
  .letterhead__footer .label {
    color: var(--brand-green);
    font-weight: 700;
  }
  /* Folder */
  .folder {
    position: absolute;
    left: 552px;
    top: 77px;
    width: 520px;
    height: 657px;
    background: linear-gradient(135deg, var(--folder-green) 0%, var(--folder-green-deep) 100%);
    border-top: 4px solid var(--white);
    border-bottom: 4px solid var(--white);
    box-sizing: border-box;
    overflow: hidden;
  }
  .folder__pattern {
    position: absolute;
    inset: 0;
    background: radial-gradient(ellipse at 60% 35%, rgba(255,255,255,0.12), rgba(255,255,255,0) 65%);
  }
  .folder__spine {
    position: absolute;
    top: 0;
    bottom: 0;
    left: 0;
    width: 40px;
  }
  .folder__brand {
    position: absolute;
    left: 0;
    right: 0;
    top: 338px;
    display: flex;
    align-items: center;
    justify-content: center;
    gap: 12px;
  }
  .folder__brand .brand-lockup__square {
    width: 24px;
    height: 24px;
    background: var(--white);
  }
  .folder__brand .brand-lockup__name {
    font-size: 30px;
    letter-spacing: 2.5px;
    color: var(--white);
  }
</style>
</head>
<body>
<main class="canvas">
  <section class="letterhead" aria-label="Letterhead">
    <div class="letterhead__pattern" role="img" aria-label="Soft grey network of connected nodes pattern"></div>
    <div class="brand-lockup">
      <span class="brand-lockup__square"></span>
      <span class="brand-lockup__name">StructaVolt</span>
    </div>
    <article class="letter">
      <p class="letter__greeting">Dear Mr. Harlow,</p>
      <div class="letter__body">
        <p>Thank you for meeting with our team last week to review the energy profile of your headquarters building. We have gathered the sensor readings from all floors and prepared a short summary of the findings, together with a set of measures that could reduce heating and cooling demand over the coming year.</p>
        <p>Our connected devices showed that several zones stay fully lit and conditioned after hours, while the ventilation runs at constant speed regardless of occupancy. Adjusting these schedules through the building platform is simple, and it would deliver savings without any change to the comfort of the people who work there every day.</p>
        <p>We propose a pilot on two floors during the next quarter. Our engineers will install additional meters, calibrate the controls and share a weekly dashboard with your facilities team. At the end of the pilot we will compare the results with the baseline and recommend how to extend the program across the whole site.</p>
        <p>Please let us know a convenient date to walk through the proposal in person. We would be glad to answer any questions and to adapt the plan to your priorities.</p>
      </div>
      <p class="letter__closing">Sincerely,</p>
      <div class="letter__signature" role="img" aria-label="Handwritten signature of Evan Harlow in green"></div>
    </article>
    <footer class="letterhead__footer">
      <div><span class="label">Phone:</span> (555) 014-2290 <span class="label">Email:</span> info@structavolt.example <span class="label">Web:</span> www.structavolt.example</div>
      <div><span class="label">social :</span> structavolt</div>
    </footer>
  </section>

  <section class="folder" aria-label="Presentation folder cover">
    <div class="folder__pattern" role="img" aria-label="Faint network of connected nodes pattern on green"></div>
    <svg class="folder__spine" width="40" height="649" viewBox="0 0 40 649" aria-hidden="true">
      <line x1="3" y1="0" x2="3" y2="649" stroke="#c6e27a" stroke-width="1"/>
      <line x1="15" y1="0" x2="15" y2="649" stroke="#9fc540" stroke-width="1"/>
      <line x1="19" y1="0" x2="19" y2="649" stroke="#c6e27a" stroke-width="1"/>
      <line x1="31" y1="0" x2="31" y2="649" stroke="#c6e27a" stroke-width="1" opacity="0.6"/>
    </svg>
    <div class="folder__brand">
      <span class="brand-lockup__square"></span>
      <span class="brand-lockup__name">StructaVolt</span>
    </div>
  </section>
</main>
</body>
</html>
```